Meadowlark Property Review is a leading provider of residential appraisal and home inspection products in S

I need a business card/logo designed that obviously describes my business. We are a residential appraisal and home inspection company in Springfield, MO. We offer residential appraisals, home inspection, pest inspection and radon gas measurement. We have been in business for 18 years and hold state certified residential appraisal licenses and OBREX certified home inspection licenses. I have a logo that I really like and will attach, but would be open to new suggestions. I like more modern designs than traditional and would like a two sided card with our services, licenses and qualifications on the back.

```html
<!DOCTYPE html>
<html lang="en">
<head>
<meta charset="utf-8">
<title>Meadowlark Property Review – Business Card</title>
<link href="https://fonts.googleapis.com/css2?family=Open+Sans:wght@400;600&display=swap" rel="stylesheet">
<style>
  :root{
    --backdrop:#3b3b3d;
    --paper:#efefed;
    --orange:#e8952a;
    --brown:#8a6b48;
    --ink:#1d1d1d;
    --white:#ffffff;
  }
  *{box-sizing:border-box;margin:0;padding:0}
  html,body{width:1200px;height:901px;overflow:hidden}
  body{
    background:var(--backdrop);
    font-family:"Open Sans",Arial,sans-serif;
    display:flex;flex-direction:column;align-items:center;justify-content:center;gap:40px;
  }
  .card{width:700px;height:400px;position:relative;overflow:hidden}
  .card--front{background:var(--paper)}
  .card--back{background:var(--orange)}

  .brand{position:absolute;display:flex;align-items:center;gap:12px;font-weight:600;font-size:30px;line-height:1.05;letter-spacing:.5px}
  .brand__mark{width:22px;height:22px;flex:none}
  .card--front .brand{left:70px;top:70px;color:var(--brown)}
  .card--front .brand__mark{background:var(--orange)}
  .card--back .brand{right:40px;top:40px;color:var(--white);text-align:left}
  .card--back .brand__mark{background:var(--white)}

  .divider{position:absolute;left:385px;top:150px;width:4px;height:220px;background:var(--orange)}

  .contact{position:absolute;left:405px;top:215px;list-style:none;font-size:17px;color:var(--ink);line-height:25px}
  .contact li{display:flex;align-items:center;gap:10px}
  .contact__icon{width:17px;height:17px;background:var(--orange);flex:none;display:flex;align-items:center;justify-content:center}
  .contact__icon svg{width:11px;height:11px;fill:var(--white)}
  .contact__plain{padding-left:27px}

  .services__title{position:absolute;left:60px;top:105px;font-size:42px;font-weight:400;color:var(--white)}
  .services{position:absolute;list-style:none;color:var(--white);font-size:19px;line-height:27px}
  .services--first{left:60px;top:165px}
  .services--second{left:390px;top:225px}
  .services li{display:flex;align-items:center;gap:12px}
  .services svg{width:18px;height:12px;flex:none}
</style>
</head>
<body>

<section class="card card--front" aria-label="Card front">
  <div class="brand"><span class="brand__mark"></span><span>Meadowlark<br>Property Review</span></div>
  <div class="divider"></div>
  <ul class="contact">
    <li><span class="contact__icon"><svg viewBox="0 0 12 12"><path d="M2 1h3l1 3-1.5 1a6 6 0 0 0 2.5 2.5L8 6l3 1v3c0 .6-.4 1-1 1A9 9 0 0 1 1 2c0-.6.4-1 1-1z"/></svg></span>417-555-0142</li>
    <li><span class="contact__icon"><svg viewBox="0 0 12 12"><path d="M3.5 1h5v3h-5zM1 5h10v4H9v2H3V9H1z"/></svg></span>417-555-0187</li>
    <li><span class="contact__icon"><svg viewBox="0 0 12 12"><path d="M3.5 0h5a1 1 0 0 1 1 1v10a1 1 0 0 1-1 1h-5a1 1 0 0 1-1-1V1a1 1 0 0 1 1-1zM4 2v7h4V2z"/></svg></span>417-555-0163</li>
    <li><span class="contact__icon"><svg viewBox="0 0 12 12"><path d="M1 2.5h10v7H1zM1.5 3 6 6.5 10.5 3v1L6 7.5 1.5 4z"/></svg></span>info@meadowlarkreview.com</li>
    <li><span class="contact__icon"><svg viewBox="0 0 12 12"><path d="M6 0a4 4 0 0 1 4 4c0 3-4 8-4 8S2 7 2 4a4 4 0 0 1 4-4zm0 2.5a1.5 1.5 0 1 0 0 3 1.5 1.5 0 0 0 0-3z"/></svg></span>Meadowlark Property Review</li>
    <li class="contact__plain">482 W Linden Avenue; Suite C</li>
    <li class="contact__plain">Springfield, MO 65807</li>
  </ul>
</section>

<section class="card card--back" aria-label="Card back">
  <div class="brand"><span class="brand__mark"></span><span>Meadowlark<br>Property Review</span></div>
  <h2 class="services__title">Services</h2>
  <ul class="services services--first">
    <li><svg viewBox="0 0 18 12"><path d="M8 0 2 6l6 6h3L5 6l6-6zM15 0 9 6l6 6h3l-6-6 6-6z" fill="#1d1d1d"/></svg>home inspection</li>
    <li><svg viewBox="0 0 18 12"><path d="M8 0 2 6l6 6h3L5 6l6-6zM15 0 9 6l6 6h3l-6-6 6-6z" fill="#1d1d1d"/></svg>property inspection</li>
    <li><svg viewBox="0 0 18 12"><path d="M8 0 2 6l6 6h3L5 6l6-6zM15 0 9 6l6 6h3l-6-6 6-6z" fill="#1d1d1d"/></svg>residential appraisal</li>
    <li><svg viewBox="0 0 18 12"><path d="M8 0 2 6l6 6h3L5 6l6-6zM15 0 9 6l6 6h3l-6-6 6-6z" fill="#1d1d1d"/></svg>termite inspection</li>
    <li><svg viewBox="0 0 18 12"><path d="M8 0 2 6l6 6h3L5 6l6-6zM15 0 9 6l6 6h3l-6-6 6-6z" fill="#1d1d1d"/></svg>radon gas measurement</li>
    <li><svg viewBox="0 0 18 12"><path d="M8 0 2 6l6 6h3L5 6l6-6zM15 0 9 6l6 6h3l-6-6 6-6z" fill="#1d1d1d"/></svg>pre purchase inspection</li>
  </ul>
  <ul class="services services--second">
    <li><svg viewBox="0 0 18 12"><path d="M8 0 2 6l6 6h3L5 6l6-6zM15 0 9 6l6 6h3l-6-6 6-6z" fill="#1d1d1d"/></svg>thermal imaging</li>
    <li><svg viewBox="0 0 18 12"><path d="M8 0 2 6l6 6h3L5 6l6-6zM15 0 9 6l6 6h3l-6-6 6-6z" fill="#1d1d1d"/></svg>mechanical inspection</li>
    <li><svg viewBox="0 0 18 12"><path d="M8 0 2 6l6 6h3L5 6l6-6zM15 0 9 6l6 6h3l-6-6 6-6z" fill="#1d1d1d"/></svg>tax appeal</li>
    <li><svg viewBox="0 0 18 12"><path d="M8 0 2 6l6 6h3L5 6l6-6zM15 0 9 6l6 6h3l-6-6 6-6z" fill="#1d1d1d"/></svg>asset evaluation</li>
    <li><svg viewBox="0 0 18 12"><path d="M8 0 2 6l6 6h3L5 6l6-6zM15 0 9 6l6 6h3l-6-6 6-6z" fill="#1d1d1d"/></svg>energy audits</li>
  </ul>
</section>

</body>
</html>
```